Bright, Bold Sydney Tutoring Business Flyer Advertisment

Lumora is an up and coming tutoring business located on Sydney's Upper North Shore catering to school students of all ages. We need a flyer designed for notice boards and letter box drops to attract new clients. Our tutors are mostly university education students who are fresh, dedicated and passionate about their areas of teaching. The flyer should exhibit a bright, bold, modern, clean cut style which would appeal to both students and parents. I have attached our logo (the flyer could reflect this colour scheme), and a PDF which outlines the information we would like to appear on the flyer. This is not set in stone, but designed to act as an extremely loose guide for your creativity !

Target Market(s)

Affluent School Students and Parents

Industry/Entity Type

Tutoring

Requirements
Must have
• Logo, $10 offer, company description.
Nice to have
• Grabbing headlines to attract new clients, such as "Feeling overwhelmed at school?". We are looking for an eye catching, clean cut and professional design that has the colours to attract kids and the tone to attract parents.

```html
<!DOCTYPE html>
<html lang="en">
<head>
<meta charset="utf-8">
<title>Lumora Tutoring Flyer</title>
<link href="https://fonts.googleapis.com/css2?family=Antonio:wght@300;400;700&display=swap" rel="stylesheet">
<style>
  :root {
    --backdrop: #5c6168;
    --paper: #ffffff;
    --paper-shade: #e4e4e4;
    --ink: #2f2f2f;
    --band: #2b2b2b;
    --band-text: #ffffff;
    --accent-blue: #3d9ad8;
    --accent-pink: #e8568f;
  }
  * { margin: 0; padding: 0; box-sizing: border-box; }
  html, body { width: 1200px; height: 1000px; overflow: hidden; }
  body {
    background: var(--backdrop);
    font-family: "Antonio", "Arial Narrow", sans-serif;
    color: var(--ink);
    position: relative;
  }
  .flyer {
    position: absolute;
    left: 262px; top: 20px;
    width: 676px; height: 955px;
    background: radial-gradient(ellipse at 50% 40%, var(--paper) 55%, var(--paper-shade) 100%);
    box-shadow: 0 2px 10px rgba(0,0,0,0.35);
    overflow: hidden;
  }
  .headline {
    position: absolute; left: 0;
    background: var(--band);
    color: var(--band-text);
    font-weight: 700;
    font-size: 25px;
    line-height: 26px;
    letter-spacing: 0;
    padding: 5px 14px 5px 33px;
    text-transform: uppercase;
    white-space: nowrap;
  }
  .headline-1 { top: 84px; }
  .headline-2 { top: 128px; }
  .headline-3 { top: 202px; }
  .description {
    position: absolute; left: 34px; top: 291px; width: 232px;
    font-size: 12.5px; line-height: 16px; font-weight: 300;
  }
  .student-photo {
    position: absolute; left: 413px; top: 25px; width: 240px; height: 485px;
  }
  .brand-name {
    position: absolute; left: 0; width: 100%; top: 598px;
    text-align: center; font-size: 50px; line-height: 60px; font-weight: 700;
    color: var(--ink);
  }
  .offer-lead {
    position: absolute; left: 0; width: 100%; top: 668px;
    text-align: center; font-size: 27px; line-height: 32px; font-weight: 300;
    white-space: nowrap;
  }
  .offer-main {
    position: absolute; left: 0; width: 100%; top: 700px;
    text-align: center; font-size: 58px; line-height: 70px; font-weight: 300;
    white-space: nowrap;
  }
  .offer-price { color: var(--accent-blue); font-weight: 700; }
  .contact-line {
    position: absolute; left: 0; width: 100%; top: 785px;
    text-align: center; font-size: 16px; line-height: 20px; font-weight: 400;
    white-space: nowrap;
  }
  .email-band {
    position: absolute; left: 0; top: 811px; width: 100%; height: 31px;
    background: var(--band); color: var(--band-text);
    text-align: center; font-size: 18px; font-weight: 700; line-height: 31px;
  }
  .website {
    position: absolute; left: 0; width: 100%; top: 862px;
    text-align: center; font-size: 38px; line-height: 46px; font-weight: 400;
    color: var(--accent-pink);
  }
  .address {
    position: absolute; left: 0; width: 100%; top: 912px;
    text-align: center; font-size: 12px; line-height: 16px; font-weight: 300;
  }
</style>
</head>
<body>
  <main class="flyer">
    <h2 class="headline headline-1">Feeling overwhelmed by the HSC?</h2>
    <h2 class="headline headline-2">Looking to improve your skills,<br>confidence and organisation?</h2>
    <h2 class="headline headline-3">Want to increase your child’s<br>engagement at school?</h2>

    <p class="description">Lumora Tutoring offers one-on-one, individualised learning experiences to maximise academic development. Our tutors are hand selected on the basis of their qualifications, expertise and passion for inspiring young learners.</p>

    <svg class="student-photo" role="img" aria-label="Photo of a smiling student with a backpack carrying books" viewBox="0 0 240 485">
      <defs>
        <linearGradient id="studentTone" x1="0" y1="0" x2="0" y2="1">
          <stop offset="0" stop-color="#3a3a3a"/>
          <stop offset="0.5" stop-color="#2a2a2a"/>
          <stop offset="0.55" stop-color="#4d5f78"/>
          <stop offset="1" stop-color="#6f7f95"/>
        </linearGradient>
      </defs>
      <rect width="240" height="485" rx="6" fill="url(#studentTone)" opacity="0.85"/>
    </svg>

    <div class="brand-name">lumora</div>

    <p class="offer-lead">Mention this advertisement to claim your</p>
    <p class="offer-main">trial session for <span class="offer-price">JUST $10!</span></p>
    <p class="contact-line">Contact us today to discuss how we can help make your learning goals a reality!</p>

    <div class="email-band">info@lumoratutoring.com.au</div>

    <div class="website">LumoraTutoring.com.au</div>
    <p class="address">Suite 4, 220 Wattle Road Lindfield, NSW 2070</p>
  </main>
</body>
</html>
```